Corporate Travel Technology Company needs new Business Card design

We need a new business card design to reflect our re-branded company. Our company is called tolvEn (pronounced tolvenn) and we provide Business Intelligence and mobile travel management solutions for the corporate travel industry. Our multinational customers use our solutions to manage large travel budgets and frequent travellers, as well as to save money and reduce risk. We'd like to see designs that use the blue and green palette as well as our corporate logo (attached below). The design should communicate innovation, insight, forward thinking, contemporary, trusted.

Target Market(s)

Large multinational corporates and Travel Agencies.

Industry/Entity Type

Business

Contact Information for Business Card

Rosalind Mercer
Chief Executive
tolvEn
Phone number - +61 (0)2 8134 2907
Email address - rosalind.mercer@tolven-example.com
Mobile number - +61 (0)438 516 702
www.tolven-example.com

Font styles to use
Other font styles liked:
• Please use font as close to corporate logo as possible

Colors
0255a3
0393ce
00a990
33b8a4
33a6d7
3176b5

Requirements
Must have
• Please include the words;
• Mobile Travel Management
• Accelerating Travel Business Insights
• Use corporate logo - although icon can be stylised if needed

```html
<!DOCTYPE html>
<html lang="en">
<head>
<meta charset="utf-8">
<title>Tolven — Business Card</title>
<link rel="stylesheet" href="https://fonts.googleapis.com/css2?family=Source+Sans+3:wght@400;600;700&display=swap">
<style>
  :root {
    --backdrop: #141414;
    --card-white: #ffffff;
    --card-blue: #2eaade;
    --brand-blue: #1f9cd8;
    --ink: #3d4b4c;
    --on-blue: #ffffff;
  }
  * { margin: 0; padding: 0; box-sizing: border-box; }
  html, body { width: 1200px; height: 900px; overflow: hidden; }
  body {
    background: var(--backdrop);
    font-family: "Source Sans 3", Arial, sans-serif;
    position: relative;
  }
  .card {
    position: absolute;
    top: 306px;
    width: 439px;
    height: 271px;
    border-radius: 12px;
  }
  .card--front { left: 149px; background: var(--card-white); }
  .card--back { left: 608px; background: var(--card-blue); }

  .brand__name {
    position: absolute;
    font-weight: 400;
    line-height: 1;
  }
  .card--front .brand__name {
    left: 26px; top: 118px;
    font-size: 46px;
    color: var(--ink);
  }
  .card--back .brand__name {
    left: 0; right: 0; top: 110px;
    text-align: center;
    font-size: 60px;
    color: var(--on-blue);
  }

  .person { position: absolute; left: 235px; top: 76px; }
  .person__name { font-size: 15.5px; font-weight: 600; color: var(--brand-blue); line-height: 18px; }
  .person__role { font-size: 12.5px; color: var(--ink); line-height: 16px; }

  .contacts { position: absolute; left: 235px; top: 131px; list-style: none; }
  .contacts li {
    display: flex; align-items: center;
    font-size: 12.2px; color: var(--ink);
    line-height: 16px;
  }
  .contacts svg { width: 9px; height: 9px; margin-right: 10px; flex: none; fill: var(--brand-blue); }

  .taglines {
    position: absolute; left: 0; right: 0; top: 195px;
    text-align: center;
    color: var(--on-blue);
    font-size: 12.5px; font-weight: 600; line-height: 16px;
  }
</style>
</head>
<body>
  <section class="card card--front">
    <p class="brand__name">Tolven</p>
    <div class="person">
      <p class="person__name">Rosalind Mercer</p>
      <p class="person__role">Chief Executive</p>
    </div>
    <ul class="contacts">
      <li><svg viewBox="0 0 10 10" aria-hidden="true"><path d="M2 0.5 L3.6 0.5 L4.2 3 L3 3.8 Q4 6 6.2 7 L7 5.8 L9.5 6.4 L9.5 8 Q9.5 9.5 8 9.5 Q0.5 9 0.5 2 Q0.5 0.5 2 0.5Z"/></svg>+61 (0)2 8134 2907</li>
      <li><svg viewBox="0 0 10 10" aria-hidden="true"><path d="M2.5 0 H7.5 V10 H2.5Z M3.4 1.2 V7.6 H6.6 V1.2Z M4.5 8.3 H5.5 V9.2 H4.5Z"/></svg>+61 (0)438 516 702</li>
      <li><svg viewBox="0 0 10 10" aria-hidden="true"><path d="M0.5 2 H9.5 V8 H0.5Z M1 2.4 L5 5.4 L9 2.4 L9 3.2 L5 6.2 L1 3.2Z" fill-rule="evenodd"/></svg>rosalind.mercer@tolven-example.com</li>
      <li><svg viewBox="0 0 10 10" aria-hidden="true"><path d="M5 0.5 A4.5 4.5 0 1 0 5 9.5 A4.5 4.5 0 1 0 5 0.5Z M5 1.4 A3.6 3.6 0 1 1 5 8.6 A3.6 3.6 0 1 1 5 1.4Z M4.6 1 H5.4 V9 H4.6Z M1 4.6 H9 V5.4 H1Z" fill-rule="evenodd"/></svg>www.tolven-example.com</li>
    </ul>
  </section>

  <section class="card card--back">
    <p class="brand__name">Tolven</p>
    <p class="taglines">Mobile Travel Management<br>Accelerating Travel Business Insights</p>
  </section>
</body>
</html>
```